English and Spanish Language School Needs a Business Card

Need a business card design a startup company called Maribel Language School. The company will offer English and Spanish conversational level courses designed to make the learner feel comfortable with grammar and vocabulary. We would like to see a logo with some colour that should communicate learning, growth.

Target Market(s)

Consumers and businesses

Industry/Entity Type

Education

Contact Information for Business Card

TBD

Font styles to use
Serif

Requirements
Must have
• Include the following
• Logo
• Name
• Title
• Cellphone Number
• Office Phone number
• Email address
• Office Address

```html
<!DOCTYPE html>
<html lang="en">
<head>
<meta charset="utf-8">
<title>Maribel Language School — Business Card</title>
<link rel="stylesheet" href="https://fonts.googleapis.com/css2?family=Varela+Round&display=swap">
<style>
  :root {
    --stage: #ecebe8;
    --card-white: #f7f7f7;
    --brand-red: #d3222f;
    --brand-red-dark: #b81c28;
    --brand-cyan: #1fb8c4;
    --shadow: rgba(0, 0, 0, 0.18);
  }
  * { box-sizing: border-box; margin: 0; padding: 0; }
  html, body {
    width: 1200px; height: 780px; overflow: hidden;
    background: var(--stage);
    font-family: "Varela Round", Arial, sans-serif;
  }
  .stage {
    position: relative; width: 1200px; height: 780px;
    display: flex; align-items: center; justify-content: center; gap: 40px;
  }
  .card {
    position: relative; width: 540px; height: 309px;
    border-radius: 16px;
    box-shadow: 0 6px 18px var(--shadow);
    overflow: hidden;
  }
  /* Front */
  .card--front { background: var(--card-white); }
  .card--front .brand {
    position: absolute; left: 36px; top: 0; bottom: 0; width: 210px;
    display: flex; flex-direction: column; justify-content: center;
    color: var(--brand-red);
  }
  .brand__name { font-size: 40px; line-height: 1; letter-spacing: -0.5px; }
  .brand__tagline { font-size: 17px; margin-top: 6px; }
  .divider {
    position: absolute; left: 262px; top: 42px; bottom: 42px; width: 1.5px;
    background: var(--brand-cyan);
  }
  .contact {
    position: absolute; left: 290px; top: 58px; right: 20px;
    color: var(--brand-cyan);
  }
  .contact__name { color: var(--brand-red); font-size: 19px; letter-spacing: 0.5px; }
  .contact__title { font-size: 13px; margin-bottom: 16px; }
  .contact__address { font-size: 13px; line-height: 1.45; margin-bottom: 8px; }
  .contact__row {
    display: flex; align-items: center; gap: 8px;
    font-size: 13px; line-height: 1; margin-top: 6px;
  }
  .icon {
    width: 16px; height: 16px; border-radius: 3px; flex: none;
    background: var(--brand-red);
    display: flex; align-items: center; justify-content: center;
  }
  .icon svg { width: 10px; height: 10px; }
  /* Back */
  .card--back {
    background: radial-gradient(ellipse at 45% 40%, var(--brand-red) 0%, var(--brand-red-dark) 100%);
    display: flex; align-items: center; justify-content: center;
  }
  .card--back .brand { color: #ffffff; text-align: left; }
  .card--back .brand__name { font-size: 76px; letter-spacing: -1px; }
  .card--back .brand__tagline { font-size: 22px; margin-top: 8px; margin-left: 4px; }
</style>
</head>
<body>
<main class="stage">
  <section class="card card--front" aria-label="Business card front">
    <div class="brand">
      <div class="brand__name">Maribel</div>
      <div class="brand__tagline">Language School</div>
    </div>
    <div class="divider"></div>
    <div class="contact">
      <div class="contact__name">DANIEL REYES</div>
      <div class="contact__title">Manager</div>
      <div class="contact__address">Your Address, 2nd Ste<br>Brookhaven, Texas 1234</div>
      <div class="contact__row">
        <span class="icon"><svg viewBox="0 0 10 10"><rect x="3" y="1" width="4" height="8" rx="0.8" fill="none" stroke="#fff" stroke-width="1"/></svg></span>
        123 456 7890
      </div>
      <div class="contact__row">
        <span class="icon"><svg viewBox="0 0 10 10"><path d="M2 1.5 L3.8 1.5 L4.4 3.4 L3.4 4.2 Q4.3 6 5.8 6.6 L6.6 5.6 L8.5 6.2 L8.5 8 Q4.5 8.5 2 4.5 Z" fill="#fff"/></svg></span>
        123 456 7890
      </div>
      <div class="contact__row">
        <span class="icon"><svg viewBox="0 0 10 10"><rect x="1" y="2.5" width="8" height="5.5" fill="none" stroke="#fff" stroke-width="1"/><path d="M1 2.5 L5 5.8 L9 2.5" fill="none" stroke="#fff" stroke-width="1"/></svg></span>
        info@maribelschool.com
      </div>
    </div>
  </section>

  <section class="card card--back" aria-label="Business card back">
    <div class="brand">
      <div class="brand__name">Maribel</div>
      <div class="brand__tagline">Language School</div>
    </div>
  </section>
</main>
</body>
</html>
```